Powerpoint design template for LUMOTEX for new digital platform

We would like to use a PowerPoint template, we would like to create a new page, we would like to create a new digital platform LUMOTEX for schools and parents for the creation of playful communication and educational tools for children to enhance their positive development, amaze them learn in a playful way. This platform is going to be the most creative, stimulating and innovative classroom, easy to use and fast to implement. Scrapbooking, collages ... Magazine, newsletters Diplomla / awards Slideshows Facebook Calendars Organizers Greetings Games ... This powerpoint template will be used essential to We are looking for a professional design, positioning our brand in the children market with an adult hearing. so you will need to find a good deal. Primary target: nurseries & schools from 0 to 18 years old and universities (in 2nd phase) Secondary target: small & medium businesses Third target: general public, and TPE If it is a color scheme, then it is suggested that it be marketed in Europe (UK, Italy, Spain) and in a 2nd Stage USA and other countries. multiple options for front page, insidious pages (multiple styles with limited text and extended text) and final contact page We need something to read, we can not do it too much, but we can not do it. , and inside pages aligned to our logo

Target Market(s)

Target 1; Education with teacher Target 2; parents and grandparents

Industry/Entity Type

Education

Font styles to use
Other font styles liked:
• not decided. but not too fancy

Requirements
Must have
• Multi page options for front page, page insides (multiple styles with limited text and extended text) and final page contact
Nice to have
• do not have a lot of ideas. We need something to read, we can not get away from it
Should not have
• not too fancy and busy: keep clarity & simplicity while reassuring on quality

```html
<!DOCTYPE html>
<html lang="en">
<head>
<meta charset="utf-8">
<title>Project Title Here – LUMOTEX</title>
<link href="https://fonts.googleapis.com/css2?family=Roboto+Condensed:wght@400;700&family=Roboto:wght@400;500&display=swap" rel="stylesheet">
<style>
  :root {
    --lime: #d8e043;
    --lime-dark: #a9c23a;
    --lime-light: #e6ec7a;
    --orange-band: #f7941d;
    --ink: #2b2b2b;
    --body: #7a7a7a;
    --white: #ffffff;
    --red: #e8173f;
    --yellow: #f7c600;
    --plum: #6f3a6a;
    --orange: #f05a22;
    --green: #9cc42a;
    --blue: #1e8fd8;
  }
  * { margin: 0; padding: 0; box-sizing: border-box; }
  html, body { width: 1200px; height: 900px; overflow: hidden; background: var(--white); }
  .slide { position: relative; width: 1200px; height: 900px; overflow: hidden; font-family: "Roboto Condensed", sans-serif; }
  .bands { position: absolute; inset: 0; }
  .slide-title {
    position: absolute; left: 30px; top: 30px;
    font-size: 46px; font-weight: 700; color: var(--ink); letter-spacing: 0.5px;
  }
  .brand { position: absolute; left: 1000px; top: 40px; width: 160px; }
  .brand-name { font-size: 34px; font-weight: 700; color: var(--ink); letter-spacing: 1px; line-height: 1; }
  .brand-tagline { margin-top: 6px; font-size: 9px; font-weight: 700; color: var(--ink); letter-spacing: 1px; line-height: 1.2; }
  .feature { position: absolute; width: 331px; }
  .feature-head { display: flex; align-items: center; height: 78px; }
  .feature-icon {
    width: 78px; height: 78px; border-radius: 50%;
    display: flex; align-items: center; justify-content: center; flex-shrink: 0;
  }
  .feature-icon svg { width: 30px; height: 30px; }
  .feature-title { margin-left: 20px; font-family: "Roboto", sans-serif; font-size: 22px; font-weight: 500; }
  .feature-text { margin-top: 32px; font-size: 21px; color: var(--body); line-height: 34.5px; }
  .feature-text span { display: block; text-align: justify; text-align-last: justify; }
  .is-red .feature-icon { background: var(--red); } .is-red .feature-title { color: var(--red); }
  .is-yellow .feature-icon { background: var(--yellow); } .is-yellow .feature-title { color: var(--yellow); }
  .is-plum .feature-icon { background: var(--plum); } .is-plum .feature-title { color: var(--plum); }
  .is-orange .feature-icon { background: var(--orange); } .is-orange .feature-title { color: var(--orange); }
  .is-green .feature-icon { background: var(--green); } .is-green .feature-title { color: var(--green); }
  .is-blue .feature-icon { background: var(--blue); } .is-blue .feature-title { color: var(--blue); }
  .footer-url, .footer-page { position: absolute; top: 852px; font-size: 24px; color: var(--ink); }
  .footer-url { left: 21px; }
  .footer-page { left: 1077px; }
</style>
</head>
<body>
<div class="slide">
  <svg class="bands" width="1200" height="900" viewBox="0 0 1200 900" aria-hidden="true">
    <polygon points="0,0 955,0 900,112 0,112" fill="var(--lime)"/>
    <polygon points="945,0 985,0 930,112 900,112" fill="var(--lime-dark)"/>
    <polygon points="975,0 1000,0 960,60" fill="var(--lime-light)"/>
    <polygon points="1040,100 1130,80 1110,120" fill="var(--lime)"/>
    <polygon points="0,834 960,834 1010,900 0,900" fill="var(--lime)"/>
    <polygon points="960,834 985,834 1035,900 1010,900" fill="var(--lime-dark)"/>
    <polygon points="990,834 1200,834 1200,900 1040,900" fill="var(--orange-band)"/>
  </svg>

  <h1 class="slide-title">PROJECT TITLE HERE</h1>

  <div class="brand">
    <div class="brand-name">LUMOTEX</div>
    <div class="brand-tagline">YOUR TAGLINE<br>GOES HERE</div>
  </div>

  <section class="feature is-red" style="left:49px; top:217px;">
    <div class="feature-head">
      <div class="feature-icon"><svg viewBox="0 0 24 24"><rect x="3" y="3" width="18" height="18" rx="3" fill="#fff"/><path d="M7 12l3.5 3.5L17 9" stroke="var(--red)" stroke-width="2.6" fill="none"/></svg></div>
      <h2 class="feature-title">Creative Strategy</h2>
    </div>
    <p class="feature-text"><span>Liquorice chupa chups applicake</span><span>apple pie cake cupcake brownie bear</span><span>claw cake gingerbread cotton candy.</span><span>Bear claw croissant apple pie. Crois-</span></p>
  </section>

  <section class="feature is-yellow" style="left:450px; top:217px;">
    <div class="feature-head">
      <div class="feature-icon"><svg viewBox="0 0 24 24"><rect x="2" y="3" width="20" height="14" rx="1.5" fill="#fff"/><rect x="4.5" y="5.5" width="15" height="9" fill="var(--yellow)"/><rect x="9" y="18" width="6" height="3" fill="#fff"/></svg></div>
      <h2 class="feature-title">Employee Desktop</h2>
    </div>
    <p class="feature-text"><span>Liquorice chupa chups applicake</span><span>apple pie cake cupcake brownie bear</span><span>claw cake gingerbread cotton candy.</span><span>Bear claw croissant apple pie. Crois-</span></p>
  </section>

  <section class="feature is-plum" style="left:842px; top:217px;">
    <div class="feature-head">
      <div class="feature-icon"><svg viewBox="0 0 24 24"><path d="M3 6h7v7l-3 6H4l2-6H3z M14 6h7v7l-3 6h-3l2-6h-3z" fill="#fff"/></svg></div>
      <h2 class="feature-title">Business Plan</h2>
    </div>
    <p class="feature-text"><span>Liquorice chupa chups applicake</span><span>apple pie cake cupcake brownie bear</span><span>claw cake gingerbread cotton candy.</span><span>Bear claw croissant apple pie. Crois-</span></p>
  </section>

  <section class="feature is-orange" style="left:49px; top:532px;">
    <div class="feature-head">
      <div class="feature-icon"><svg viewBox="0 0 24 24"><path d="M4 3h16v9c0 5-4 8-8 10-4-2-8-5-8-10z" fill="#fff"/><path d="M12 6h5v6c0 3-2 5-5 6.5z" fill="var(--orange)"/></svg></div>
      <h2 class="feature-title">System Protection</h2>
    </div>
    <p class="feature-text"><span>Liquorice chupa chups applicake</span><span>apple pie cake cupcake brownie bear</span><span>claw cake gingerbread cotton candy.</span><span>Bear claw croissant apple pie. Crois-</span></p>
  </section>

  <section class="feature is-green" style="left:450px; top:532px;">
    <div class="feature-head">
      <div class="feature-icon"><svg viewBox="0 0 24 24"><rect x="1.5" y="7" width="21" height="11" rx="5.5" fill="#fff"/><path d="M6 12.5h4M8 10.5v4" stroke="var(--green)" stroke-width="1.8"/><circle cx="15.5" cy="11.5" r="1.2" fill="var(--green)"/><circle cx="18" cy="13.5" r="1.2" fill="var(--green)"/></svg></div>
      <h2 class="feature-title">Fun Games</h2>
    </div>
    <p class="feature-text"><span>Liquorice chupa chups applicake</span><span>apple pie cake cupcake brownie bear</span><span>claw cake gingerbread cotton candy.</span><span>Bear claw croissant apple pie. Crois-</span></p>
  </section>

  <section class="feature is-blue" style="left:842px; top:532px;">
    <div class="feature-head">
      <div class="feature-icon"><svg viewBox="0 0 24 24"><circle cx="12" cy="4.5" r="2.2" fill="none" stroke="#fff" stroke-width="2"/><path d="M12 7v13M8 10h8M4 14c0 4 4 6 8 6s8-2 8-6" stroke="#fff" stroke-width="2" fill="none"/></svg></div>
      <h2 class="feature-title">Data Analysis</h2>
    </div>
    <p class="feature-text"><span>Liquorice chupa chups applicake</span><span>apple pie cake cupcake brownie bear</span><span>claw cake gingerbread cotton candy.</span><span>Bear claw croissant apple pie. Crois-</span></p>
  </section>

  <div class="footer-url">www.lumotex.com</div>
  <div class="footer-page">Page : 01</div>
</div>
</body>
</html>
```